New banner graphics for Tondix.com website

I've developed a software tool that helps businesses ensure they are working on their most valuable and important work.

I would like a banner graphic for my home page (www.tondix.com) that can somehow capture the value of focus and intentional outcomes.

I had an initial thought of a starry sky that shifts focus to a few bright stars, but while that might sound ok, I think my idea is lame hence I'm coming to you guys.

My sites two primary colors are a soft purple and gray.
#919EC1(purple)
#9E9E9E (gray)

Target Market(s)

B2B for enterprises. Typical customers are CFOs, CIOs/Heads of IT

Industry/Entity Type

Business Software

Number of Pages Required

1 page

Font styles to use
Sans Serif

Colors
b8a6cd
cedeed

Requirements
Must have
• I use Divi as my Wordpress theme and the current main landing page can be seen at www.tondix.com.
• My logo colors are:
• #919EC1(purple)
• #9E9E9E (gray)
Should not have
• Lots of distraction or visual "noise". I want to re-enforce the message that my software is focused on their business and not my products or website.

```html
<!DOCTYPE html>
<html lang="en">
<head>
<meta charset="UTF-8">
<title>Is Your Business Strategy</title>
<link rel="stylesheet" href="https://fonts.googleapis.com/css2?family=Roboto+Slab:wght@700&family=Raleway:ital,wght@0,400;0,700;1,400&display=swap">
<style>
  :root {
    --peach: #f6d2c2;
    --blush: #eab6ad;
    --mauve: #c48fb0;
    --plum: #9a6a9c;
    --headline: #ffffff;
    --label-purple: #8a2f9c;
    --connector: #ffffff;
    --answer-ink: #262228;
  }
  * { margin: 0; padding: 0; box-sizing: border-box; }
  html, body { width: 1200px; height: 675px; overflow: hidden; }
  body { background: var(--peach); }

  .banner {
    position: relative;
    width: 1200px;
    height: 675px;
    overflow: hidden;
  }

  .bokeh-backdrop {
    position: absolute;
    inset: 0;
    background:
      radial-gradient(circle at 88% 12%, rgba(154,106,156,0.75) 0, rgba(154,106,156,0) 22%),
      radial-gradient(circle at 62% 30%, rgba(154,106,156,0.7) 0, rgba(154,106,156,0) 20%),
      radial-gradient(circle at 20% 8%, rgba(196,143,176,0.6) 0, rgba(196,143,176,0) 20%),
      radial-gradient(circle at 8% 55%, rgba(154,106,156,0.55) 0, rgba(154,106,156,0) 22%),
      radial-gradient(circle at 80% 55%, rgba(154,106,156,0.6) 0, rgba(154,106,156,0) 18%),
      radial-gradient(circle at 55% 95%, rgba(196,143,176,0.5) 0, rgba(196,143,176,0) 25%),
      radial-gradient(circle at 30% 40%, rgba(255,236,225,0.8) 0, rgba(255,236,225,0) 25%),
      radial-gradient(circle at 75% 25%, rgba(255,236,225,0.7) 0, rgba(255,236,225,0) 18%),
      linear-gradient(160deg, var(--blush) 0%, var(--peach) 45%, var(--mauve) 100%);
  }

  .headline {
    position: absolute;
    top: 208px;
    left: 0;
    width: 1140px;
    text-align: center;
    font-family: "Roboto Slab", serif;
    font-weight: 700;
    font-size: 40px;
    color: var(--headline);
    text-shadow: 1px 2px 4px rgba(80, 40, 60, 0.45);
  }

  .contrast-list {
    position: absolute;
    top: 323px;
    left: 0;
    display: grid;
    grid-template-columns: 418px 102px auto;
    grid-auto-rows: 40px;
    align-items: center;
    font-family: "Raleway", sans-serif;
    font-size: 25px;
    text-transform: uppercase;
    white-space: nowrap;
  }

  .strength {
    text-align: right;
    color: var(--label-purple);
    font-weight: 400;
  }

  .connector {
    padding-left: 35px;
    color: var(--connector);
    font-weight: 700;
    text-shadow: 1px 1px 3px rgba(80, 40, 60, 0.45);
  }

  .weakness {
    color: var(--answer-ink);
    font-style: italic;
    font-weight: 400;
  }
</style>
</head>
<body>
  <main class="banner">
    <div class="bokeh-backdrop" role="img" aria-label="Soft-focus bokeh of glowing peach and purple light circles"></div>

    <h1 class="headline">Is Your Business Strategy</h1>

    <div class="contrast-list">
      <span class="strength">Written down</span>
      <span class="connector">or</span>
      <span class="weakness">Loose thoughts – on the&nbsp; best of days</span>

      <span class="strength">Driving projects</span>
      <span class="connector">or</span>
      <span class="weakness">Just a set of slides tacked to walls</span>

      <span class="strength">Shared with the team</span>
      <span class="connector">or</span>
      <span class="weakness">Kept top secret just to be safe</span>

      <span class="strength">Measurable</span>
      <span class="connector">or</span>
      <span class="weakness">More art than science</span>
    </div>
  </main>
</body>
</html>
```